Website & Logo The full package New Business new design and idea

Word Press

Simple, clean and very professional and approachable if possible

I am looking for a full business concept from logo to colour pallet and everything in between.
Brand new business concept, the successful applicant may continue on as our outsourced point person for all future work.

I will have an animated explainer video going over the four keys to business success Staff, Product & Services, Marketing, Sales and why the need a coach just like a sporting team to stay focused and clear on measurable outcomes.

Just added script (pdf attachment) i will be using for the explainer video at top of site.
Updates

Target Market(s)

Small business owners in Australia

Industry/Entity Type

Business Consultant

Number of Pages Required

1 page

Font styles to use
Sans Serif

Colors

Designer to choose colors to be used in the design.

Requirements
Must have
• Word press using Divi platform
• Ball park as per pdf uploaded
• Must work on all devices
• Social links
• Clear and straight forward movement through site
• Great capture of name and email,
• Free Download
• 10 Things you can start today in your small business to get you going again!
Nice to have
• clean one page potentially
• Free files and resources page
Should not have
• boring old menu and old framing

```html
<!DOCTYPE html>
<html lang="en">
<head>
<meta charset="utf-8">
<title>Clear Course Business Coach</title>
<link href="https://fonts.googleapis.com/css2?family=Roboto:wght@300;400;500;700&display=swap" rel="stylesheet">
<style>
:root{
  --blue:#3a5bd9;
  --blue-dark:#2f4cc4;
  --blue-light:#5a7bf0;
  --blue-pale:#c3cdf3;
  --ink:#333b4a;
  --grey-text:#6b6f78;
  --grey-bg:#f4f4f4;
  --white:#ffffff;
}
*{box-sizing:border-box;margin:0;padding:0}
html,body{width:1200px;height:4087px;overflow:hidden}
body{font-family:'Roboto',sans-serif;color:var(--ink);background:var(--white);position:relative}
.abs{position:absolute}
a{color:var(--blue);text-decoration:underline}
.heading{font-weight:500;color:var(--blue);font-size:27px;letter-spacing:.2px}
.body-text{font-size:15px;line-height:27px;color:var(--ink);font-weight:300}
.photo{border:none}
.frame{background:var(--blue)}

/* hero */
.hero-band{left:419px;top:0;width:781px;height:624px;background:linear-gradient(135deg,#3d5fe0,#2c49c4 60%,#4a6bea)}
.main-nav{left:360px;top:40px;display:flex;gap:22px;font-size:14px;font-weight:700;color:var(--white);letter-spacing:.3px}
.main-nav .active{color:var(--blue);border-bottom:2px solid var(--blue);padding-bottom:3px}
.vertical-title{left:90px;top:111px;width:130px;height:460px}
.vertical-title span{position:absolute;left:0;top:0;transform-origin:0 0;transform:translate(0,460px) rotate(-90deg);white-space:nowrap;font-size:52px;font-weight:500;line-height:58px;color:var(--blue-pale)}
.hero-photo{left:240px;top:95px;width:827px;height:425px;background:linear-gradient(120deg,#555b66,#3b3f48 50%,#6a7080)}
.hero-title{color:var(--white);font-weight:700;font-size:56px;line-height:1;white-space:nowrap}
.play{left:387px;top:487px;width:58px;height:58px;border-radius:50%;background:var(--white);box-shadow:0 4px 12px rgba(0,0,0,.25)}
.social-dot{width:16px;height:16px;border-radius:50%;border:2px solid var(--white)}
.side-arrow{left:1152px;width:38px;height:38px;border-radius:50%;border:2px solid var(--white)}

/* cards */
.card{background:var(--white);box-shadow:0 4px 18px rgba(0,0,0,.08);text-align:center;font-size:15px;line-height:27px;color:var(--grey-text)}
.card p{padding:40px 30px 0}
.card .go{position:absolute;right:28px;bottom:28px;width:24px;height:24px;border-radius:50%;border:1.5px solid var(--blue)}
.card.featured{background:linear-gradient(135deg,#4466e6,#3a5bd9 60%,#5a7bf0);color:var(--white);font-size:20px;line-height:32px}
.card.featured .go{border-color:var(--white)}

/* newsletter */
.newsletter{left:0;top:2346px;width:1200px;height:104px;background:linear-gradient(90deg,#3f62e2,#4f70ec 50%,#3a5bd9)}
.field{height:40px;border:1.5px solid var(--white);border-radius:4px;color:#dfe5ff;font-size:11px;font-style:italic;padding:12px 22px}
.signup-btn{left:963px;top:2379px;width:146px;height:40px;background:var(--white);border-radius:4px;color:var(--blue);font-size:20px;font-weight:500;text-align:center;line-height:40px}

/* pricing */
.plan{width:193px;height:279px;border:3px solid var(--blue);background:var(--white)}
.plan .top{height:178px;background:var(--blue);display:flex;align-items:center;justify-content:center}
.plan .label{height:95px;line-height:60px;text-align:center;font-size:15px;font-weight:500;color:var(--ink)}

/* footer */
.footer{left:0;top:3758px;width:1200px;height:329px;background:linear-gradient(180deg,#3d5fe0,#3553d2)}
.footer-nav{display:flex;gap:24px;font-size:15px;font-weight:500;color:var(--white)}
.foot-social{width:36px;height:36px;border-radius:50%;border:1.5px solid var(--white)}
</style>
</head>
<body>

<!-- Hero -->
<div class="abs hero-band"></div>
<nav class="abs main-nav">
  <span class="active">HOME</span><span>ABOUT US</span><span>HOW IT WORKS</span><span>APPLICATION</span><span>CONTACT US</span>
</nav>
<div class="abs vertical-title"><span>CLEAR COURSE<br>BUSINESS COACH</span></div>
<div class="abs hero-photo photo" role="img" aria-label="Coach presenting a chart to a small team around a table"></div>
<div class="abs hero-title" style="left:330px;top:248px">CLEAR COURSE</div>
<div class="abs hero-title" style="left:519px;top:300px">BUSINESS COACH</div>
<div class="abs play"><svg width="58" height="58" viewBox="0 0 58 58"><path d="M23 17 L40 29 L23 41 Z" fill="#3a5bd9"/></svg></div>
<div class="abs social-dot" style="left:1021px;top:570px" aria-label="Social link"></div>
<div class="abs social-dot" style="left:1052px;top:570px" aria-label="Social link"></div>
<div class="abs social-dot" style="left:1087px;top:570px" aria-label="Social link"></div>
<div class="abs side-arrow" style="top:546px"><svg width="34" height="34" viewBox="0 0 34 34"><path d="M10 17h14M19 12l5 5-5 5" stroke="#fff" stroke-width="2" fill="none"/></svg></div>
<div class="abs side-arrow" style="top:586px"><svg width="34" height="34" viewBox="0 0 34 34"><path d="M24 17H10M15 12l-5 5 5 5" stroke="#fff" stroke-width="2" fill="none"/></svg></div>

<!-- About us -->
<h2 class="abs heading" style="left:181px;top:734px">ABOUT US</h2>
<p class="abs body-text" style="left:181px;top:787px;width:395px">Clear Course Business Coach is here to help, support and turn your small business around, It may not be easy, it maynot be pretty, it may not be conventional or what you want to hear but my only goal is to help you succeed in your small business struggling in Australia.</p>
<div class="abs" style="left:181px;top:946px;font-size:15px"><a>FREE DOWNLOAD</a>
  <svg width="16" height="16" viewBox="0 0 16 16" style="margin-left:6px;vertical-align:-2px"><path d="M8 2v8M4 7l4 4 4-4M3 14h10" stroke="#3a5bd9" stroke-width="2" fill="none"/></svg></div>
<div class="abs frame" style="left:694px;top:695px;width:407px;height:254px"></div>
<div class="abs photo" style="left:676px;top:714px;width:408px;height:254px;background:linear-gradient(120deg,#e9ecf2,#b9c3d4 55%,#8a9ab3);box-shadow:0 10px 25px rgba(0,0,0,.18)" role="img" aria-label="Presenter at a whiteboard with an attentive audience"></div>

<!-- Snapshot -->
<div class="abs" style="left:0;top:1041px;width:1200px;height:453px;background:var(--grey-bg)"></div>
<h2 class="abs heading" style="left:0;top:1074px;width:1200px;text-align:center">AUSTRALIAN SMALL BUSINESS SNAPSHOT</h2>
<div class="abs frame" style="left:113px;top:1147px;width:408px;height:254px"></div>
<div class="abs photo" style="left:95px;top:1166px;width:410px;height:254px;background:linear-gradient(90deg,#f1f1ee,#dcdcd6 45%,#f4f4f1);box-shadow:0 10px 25px rgba(0,0,0,.18)" role="img" aria-label="Man sketching business strategy diagrams on a whiteboard"></div>
<div class="abs body-text" style="left:621px;top:1144px;width:490px">
  <p>It’s an extremely sad sign of the times when you’re confronted with a myriad of ‘for lease’ signs in shop windows along major shopping hubs.</p>
  <p style="margin-top:27px">What is the Small Business Failure Rate?<br>20% of small businesses fail in their first year<br>30% of small business fail in their second year<br>50% of small businesses fail after five years in business.<br>Finally, 70% of small business owners fail in their 10th year in business</p>
</div>
<div class="abs" style="left:621px;top:1438px;font-size:15px"><a>READ MORE</a></div>

<!-- How it works -->
<h2 class="abs heading" style="left:0;top:1568px;width:1200px;text-align:center">HOW IT ALL WORKS</h2>
<p class="abs" style="left:220px;top:1625px;width:760px;text-align:center;font-size:15px;line-height:27px;color:#8a8d94;font-weight:500">With your permission I breakdown your business, Staff, Products / Services, Marketing and Sales. Under each of these four key components are up to 30 or more components including your staff training and experience, business financials, public exposure and engagement with target market, current marketing and processes required to make income.</p>
<h3 class="abs" style="left:0;top:1764px;width:1200px;text-align:center;font-size:28px;font-weight:400;color:#4a4f5a">Activates includes</h3>

<div class="abs card featured" style="left:95px;top:1838px;width:316px;height:195px"><p style="padding-top:36px">Understanding market trends and embracing a SWOT analysis</p><span class="go"></span></div>
<div class="abs card" style="left:460px;top:1862px;width:276px;height:171px"><p>Getting a measurable base line of the financials and existing marketing.</p><span class="go"></span></div>
<div class="abs card" style="left:784px;top:1862px;width:276px;height:171px"><p>Discussing the past ups and downs and looking forward to the future</p><span class="go"></span></div>
<div class="abs card" style="left:136px;top:2108px;width:275px;height:169px"><p style="padding-top:36px">Looking into the staff for potential opportunities or training</p><span class="go"></span></div>
<div class="abs card" style="left:460px;top:2108px;width:276px;height:169px"><p style="padding-top:36px">Looking to establish a mastermind local group with a successful business</p><span class="go"></span></div>
<div class="abs card" style="left:784px;top:2108px;width:276px;height:169px"><p style="padding-top:36px">Creating and applying marketing objectives</p><span class="go"></span></div>

<!-- Newsletter -->
<div class="abs newsletter"></div>
<div class="abs" style="left:100px;top:2382px;font-size:27px;font-weight:500;color:var(--white)">Signup for newsletter</div>
<div class="abs field" style="left:384px;top:2379px;width:222px">Name</div>
<div class="abs field" style="left:628px;top:2379px;width:313px">Enter your email address</div>
<div class="abs signup-btn">SIGN UP</div>

<!-- Application -->
<div class="abs" style="left:0;top:2450px;width:1200px;height:413px;background:var(--grey-bg)"></div>
<h2 class="abs heading" style="left:92px;top:2567px">APPLICATION</h2>
<p class="abs body-text" style="left:92px;top:2634px;width:410px">Placements are strictly limited to 28 per quarter as they are all managed personally for the best possible outcomes.</p>
<div class="abs" style="left:92px;top:2751px;font-size:15px"><a>READ MORE</a></div>
<div class="abs frame" style="left:682px;top:2515px;width:408px;height:251px"></div>
<div class="abs photo" style="left:663px;top:2533px;width:408px;height:254px;background:linear-gradient(180deg,#d9dadc,#9ea2a8 55%,#f0f0f0);box-shadow:0 10px 25px rgba(0,0,0,.18)" role="img" aria-label="Candidates in suits seated in a row waiting for interviews"></div>

<!-- Pricing -->
<h2 class="abs heading" style="left:0;top:2936px;width:1172px;text-align:center">PRICING</h2>
<h3 class="abs" style="left:105px;top:3042px;width:460px;text-align:center;font-size:33px;font-weight:500;color:#333">FREE</h3>
<p class="abs" style="left:105px;top:3094px;width:460px;text-align:center;font-size:15px;line-height:27px;color:var(--grey-text)">Clear Course Business Coach is offering 4 FREE 12-week coaching one on one support program every 3 months to struggling businesses in 2019 as our way of giving back and helping others in need, just fill out the information sheet and we will let you know as soon as possible</p>

<div class="abs plan" style="left:632px;top:3030px"><div class="top">
  <svg width="90" height="90" viewBox="0 0 90 90" fill="none" stroke="#fff" stroke-width="3"><ellipse cx="45" cy="45" rx="40" ry="15"/><ellipse cx="45" cy="45" rx="40" ry="15" transform="rotate(60 45 45)"/><ellipse cx="45" cy="45" rx="40" ry="15" transform="rotate(-60 45 45)"/><circle cx="45" cy="45" r="5"/></svg>
</div><div class="label">FREE</div></div>
<div class="abs plan" style="left:867px;top:3030px"><div class="top">
  <svg width="96" height="90" viewBox="0 0 96 90" fill="none" stroke="#fff" stroke-width="3"><rect x="30" y="8" width="36" height="36" transform="rotate(15 48 26)"/><path d="M40 28l6 6 12-14"/><path d="M8 60h18l14 8h22c4 0 4 6 0 6H44M26 74l20 8 40-20c3-3 0-8-4-6L60 64"/></svg>
</div><div class="label">SPECIAL OFFER</div></div>
<div class="abs plan" style="left:1101px;top:3030px"><div class="top" style="justify-content:flex-start;padding-left:28px">
  <svg width="80" height="80" viewBox="0 0 80 80" fill="none" stroke="#fff" stroke-width="3"><path d="M4 16h72v14a10 10 0 0 0 0 20v14H4V50a10 10 0 0 0 0-20z"/><path d="M44 18v6M44 32v6M44 46v6M44 60v2"/></svg>
</div><div class="label" style="text-align:left;padding-left:30px">JUST A BEGINNING</div></div>
<div class="abs" style="left:611px;top:3117px;width:48px;height:48px;border-radius:50%;background:var(--white);box-shadow:0 3px 10px rgba(0,0,0,.2)"><svg width="48" height="48" viewBox="0 0 48 48"><path d="M30 24H18M23 18l-6 6 6 6" stroke="#3a5bd9" stroke-width="3" fill="none"/></svg></div>

<!-- About me -->
<div class="abs" style="left:0;top:3349px;width:1200px;height:409px;background:var(--grey-bg)"></div>
<div class="abs" style="left:136px;top:3430px;width:264px;height:260px;border:3px solid var(--blue)"></div>
<div class="abs photo" style="left:159px;top:3396px;width:198px;height:362px;border-radius:90px 90px 0 0;background:linear-gradient(180deg,#c9d7ea,#8fa9cc 50%,#7d8799)" role="img" aria-label="Portrait of the coach standing, hands in pockets"></div>
<h2 class="abs heading" style="left:481px;top:3404px">ABOUT ME</h2>
<p class="abs" style="left:481px;top:3458px;width:620px;font-size:15px;line-height:43px;color:var(--ink);font-weight:300">I am not superman, I just found myself absorbing information over the past 10 years through some mentors and personal development and see so many small business owners struggling and I got sick of telling myself how I would change things that I eventually approached some businesses for free and asked if they needed a hand and they were over the moon.</p>
<div class="abs" style="left:481px;top:3696px;font-size:15px"><a>10 THINGS YOU CAN START TODAY IN YOUR SMALL BUSINESS TO GET YOU GOING AGAIN!</a></div>

<!-- Footer -->
<footer class="abs footer">
  <div class="abs" style="left:0;top:34px;width:1192px;text-align:center;font-size:33px;font-weight:500;color:var(--white)">CLEAR COURSE BUSINESS COACH</div>
  <nav class="abs footer-nav" style="left:0;top:111px;width:1192px;justify-content:center"><span>HOME</span><span>ABOUT US</span><span>HOW IT WORKS</span><span>APPLICATION</span><span>CONTACT US</span></nav>
  <div class="abs" style="left:0;top:162px;width:1192px;text-align:center;font-size:16px;color:var(--white)">
    <svg width="13" height="13" viewBox="0 0 16 16" style="vertical-align:-1px"><path d="M3 1l3 3-2 2c1 3 3 5 6 6l2-2 3 3-2 3C7 15 1 9 1 3z" fill="#fff"/></svg> +61 7000 4821&nbsp;&nbsp;
    <svg width="14" height="12" viewBox="0 0 16 12" style="vertical-align:-1px"><rect x="0" y="0" width="16" height="12" fill="#fff"/><path d="M0 0l8 6 8-6" stroke="#3a5bd9" stroke-width="1.5" fill="none"/></svg> hello@clearcoursecoach.com&nbsp;&nbsp;
    <svg width="13" height="13" viewBox="0 0 16 16" style="vertical-align:-1px"><path d="M15 1L1 7l6 2 2 6z" fill="#fff"/></svg> 22 Harbour Lane, Northgate, QLD 4013
  </div>
  <div class="abs foot-social" style="left:507px;top:204px" aria-label="Social link"></div>
  <div class="abs foot-social" style="left:582px;top:204px" aria-label="Social link"></div>
  <div class="abs foot-social" style="left:656px;top:204px" aria-label="Social link"></div>
  <div class="abs" style="left:0;top:291px;width:1192px;text-align:center;font-size:11px;color:var(--white)">© Copyright 2018 Clear Course Business Coach. All Rights Reserved &nbsp; | &nbsp; Privacy Policy.</div>
</footer>

</body>
</html>
```